New Fun, Positive, energised looking Business Card Needed for High Achiever Coach

I am looking for a two sided full colour business card. I am self employed and have recently re branded my 1-2-1 work re-vitalising high achievers. My target client base for these cards is therefore high achievers - usually aged 40 -55, they are often entrepreneurs, CEO or work in banking and finance and 2/3 are male. I work with them on 90 day or 6 month coaching programs to help them live their success in a healthier, more sustainable and fulfiiled way. They pay for this privately so though they are corporate types the cards need not look 'corporate'. I want to portray the idea of transformation, vitality and re-connecting.
You can get a feel for the look I like on my new website: morvenlisk.co.uk
I want to use this logo with strapline (Re-Vitalising High Achievers) (I purchased off Logoharbor) and font/ colours (the turquoise and green).
Details to include on the card:
www.morvenlisk.co.uk
+44 7915 302618
morven@morvenlisk.co.uk
skype: morvenlisk
I'd also like to include:
Do you struggle to switch off? Want to be healthier and feel fitter? Want closer relationships? More clarity over the direction you are headed? I can help you do these things using integrated mind-body techniques. Visit morvenlisk.co.uk TODAY to apply for a FREE Breakthrough session.
BUT if that is too much text for a card I am open to advice/ammendments.
Updates
Thanks for your design - I am considering them. PLease change the wording to :

```html
<!DOCTYPE html>
<html lang="en">
<head>
<meta charset="utf-8">
<title>Morven Lisk – Business Card</title>
<link rel="stylesheet" href="https://fonts.googleapis.com/css2?family=Open+Sans:wght@400;700&display=swap">
<style>
  :root {
    --green: #62bd6c;
    --turquoise: #08a4c9;
    --white: #ffffff;
    --stage: #e7e8ee;
  }
  * { box-sizing: border-box; margin: 0; padding: 0; }
  html, body { width: 1200px; height: 987px; overflow: hidden; }
  body {
    background: var(--stage);
    font-family: "Open Sans", Arial, sans-serif;
    position: relative;
  }
  .card {
    position: absolute;
    left: 220px;
    width: 760px;
    height: 434px;
    border-radius: 26px;
    overflow: hidden;
    box-shadow: 0 6px 18px rgba(0,0,0,0.12);
  }
  .card--front { top: 40px; background: var(--white); }
  .card--back { top: 513px; background: var(--green); }

  /* Front */
  .front__band-green {
    position: absolute; left: 0; right: 0; top: 238px; height: 122px;
    background: var(--green);
  }
  .front__band-blue {
    position: absolute; left: 0; right: 0; bottom: 0; height: 74px;
    background: var(--turquoise);
  }
  .brand {
    position: absolute; left: 0; right: 0; top: 40px;
    display: flex; flex-direction: column; align-items: center;
  }
  .brand__dot {
    width: 100px; height: 100px; border-radius: 50%;
    background: var(--green);
  }
  .brand__name {
    margin-top: 18px;
    font-weight: 700; font-size: 44px; line-height: 1;
    color: var(--turquoise);
  }
  .contact {
    position: absolute; left: 0; right: 0; top: 262px;
    display: flex; flex-direction: column; align-items: center; gap: 14px;
    color: var(--white); font-size: 24px;
  }
  .contact__row { display: flex; gap: 36px; align-items: center; }
  .contact__item { display: flex; align-items: center; gap: 9px; }
  .contact__icon { width: 22px; height: 22px; flex: none; }
  .contact__square { width: 18px; height: 18px; background: var(--turquoise); border: 2px solid var(--white); border-radius: 3px; }
  .website {
    position: absolute; left: 0; right: 0; bottom: 0; height: 74px;
    display: flex; align-items: center; justify-content: center;
    color: var(--white); font-size: 30px; letter-spacing: 1px;
  }

  /* Back */
  .back__brand {
    position: absolute; left: 30px; top: 0; width: 270px; height: 100%;
    display: flex; flex-direction: column; align-items: center; justify-content: center;
  }
  .back__brand .brand__dot { background: var(--white); width: 96px; height: 96px; }
  .back__brand .brand__name { color: var(--white); font-size: 36px; }
  .back__divider {
    position: absolute; left: 314px; top: 70px; width: 2px; height: 294px;
    background: linear-gradient(to bottom, transparent, rgba(255,255,255,0.8), transparent);
  }
  .pitch {
    position: absolute; left: 338px; top: 66px; width: 400px;
    color: var(--white); font-size: 18px; line-height: 1.45;
  }
  .pitch p + p { margin-top: 12px; }
  .pitch strong { font-weight: 700; }
</style>
</head>
<body>

<section class="card card--front" aria-label="Business card front">
  <div class="front__band-green"></div>
  <div class="front__band-blue"></div>

  <div class="brand">
    <div class="brand__dot"></div>
    <div class="brand__name">Morven Lisk</div>
  </div>

  <div class="contact">
    <div class="contact__item">
      <svg class="contact__icon" viewBox="0 0 24 24" aria-hidden="true">
        <circle cx="12" cy="12" r="10.5" fill="none" stroke="#fff" stroke-width="1.8"/>
        <path d="M9 7.5c.6-.4 1.2-.2 1.5.4l.8 1.6c.2.5 0 1-.4 1.3l-.6.4c.5 1.2 1.4 2.1 2.6 2.6l.4-.6c.3-.4.8-.6 1.3-.4l1.6.8c.6.3.8.9.4 1.5-.6 1-1.6 1.5-2.7 1.2-2.8-.8-5-3-5.8-5.8-.3-1.1.2-2.1 1.2-2.7z" fill="#fff"/>
      </svg>
      <span>+44 7915 302618</span>
    </div>
    <div class="contact__row">
      <div class="contact__item">
        <span class="contact__square" aria-hidden="true"></span>
        <span>morvenlisk</span>
      </div>
      <div class="contact__item">
        <svg class="contact__icon" viewBox="0 0 24 24" aria-hidden="true">
          <rect x="2" y="5" width="20" height="14" rx="2" fill="#fff"/>
          <path d="M3 6.5l9 6.5 9-6.5" fill="none" stroke="#62bd6c" stroke-width="1.8"/>
        </svg>
        <span>morven@morvenlisk.co.uk</span>
      </div>
    </div>
  </div>

  <div class="website">www.morvenlisk.co.uk</div>
</section>

<section class="card card--back" aria-label="Business card back">
  <div class="back__brand">
    <div class="brand__dot"></div>
    <div class="brand__name">Morven Lisk</div>
  </div>
  <div class="back__divider"></div>
  <div class="pitch">
    <p>Finding it hard to slow down?<br>
       Want more energy and better health?<br>
       Want stronger connections at home?<br>
       A clearer sense of where you are going?</p>
    <p>I can guide you there with joined-up mind and body methods.</p>
    <p>Visit <strong>morvenlisk.co.uk</strong> TODAY to book a FREE first session.</p>
  </div>
</section>

</body>
</html>
```